Veltrano.co - Polar Expeditions Specialists

We need a modern, visually striking business card for Veltrano.co, a company specialized in selling expedition cruises to the most remote regions on Earth, with a focus on the Arctic and Antarctica. The design should instantly communicate that the cardholder is an expert in polar travel. Use clean, premium aesthetics with cool tones like icy blue and white, possibly incorporating polar imagery (ice, glaciers, penguins, etc.)

Attached the logo

Contact Information for Business Card

Feels high-end and trustworthy.. Visually memorable — encourages people to keep it

Colors
0054AA
0677BA
7BADD7
CADEEF
E8F1F8

Requirements
Must have
• ice, glaciers, penguins, montains
Nice to have
• modern, transparente,

```html
<!DOCTYPE html>
<html lang="en">
<head>
<meta charset="utf-8">
<title>Veltrano.co Business Card</title>
<link rel="stylesheet" href="https://fonts.googleapis.com/css2?family=Poppins:wght@400;500;700&family=Roboto:wght@400&display=swap">
<style>
  :root {
    --stage: #3d3d3d;
    --paper: #ffffff;
    --brand-blue: #3676b7;
    --deep-blue: #0054aa;
    --ice-blue: #7badd7;
    --frost: #cadeef;
    --mist: #e8f1f8;
    --back-text: #a6dcf2;
    --ink-grey: #3a3a3a;
  }
  * { box-sizing: border-box; margin: 0; padding: 0; }
  html, body { width: 1200px; height: 803px; overflow: hidden; }
  body {
    background: var(--stage);
    display: flex;
    align-items: center;
    justify-content: center;
    gap: 40px;
  }
  .card {
    width: 560px;
    height: 320px;
    border-radius: 22px;
    position: relative;
    overflow: hidden;
    box-shadow: 0 14px 30px rgba(0,0,0,.35);
  }
  .card-front { background: var(--paper); }
  .card-back { background: var(--brand-blue); }

  .front-info {
    position: absolute;
    left: 38px;
    top: 42px;
    width: 290px;
    color: var(--brand-blue);
  }
  .brand-name {
    font-family: 'Poppins', sans-serif;
    font-weight: 700;
    font-size: 40px;
    line-height: 1;
    letter-spacing: .5px;
  }
  .brand-tagline {
    font-family: 'Poppins', sans-serif;
    font-weight: 500;
    font-size: 11.5px;
    margin-top: 6px;
    letter-spacing: .4px;
  }
  .person-name {
    font-family: 'Poppins', sans-serif;
    font-weight: 700;
    font-size: 20px;
    margin-top: 26px;
  }
  .person-title {
    font-family: 'Roboto', sans-serif;
    font-size: 11px;
    color: #777;
    margin-top: 1px;
  }
  .address {
    font-family: 'Roboto', sans-serif;
    font-size: 12px;
    color: var(--ink-grey);
    margin-top: 12px;
    line-height: 1.35;
  }
  .contact-list {
    list-style: none;
    margin-top: 10px;
    font-family: 'Roboto', sans-serif;
    font-size: 12px;
    color: var(--ink-grey);
    line-height: 1.35;
  }
  .contact-list li { display: flex; align-items: center; gap: 7px; }
  .contact-icon { width: 11px; height: 11px; flex: none; }

  .front-art {
    position: absolute;
    right: 36px;
    top: 48px;
    width: 200px;
    height: 200px;
    border-radius: 50%;
    background: radial-gradient(circle at 40% 35%, var(--ice-blue), var(--brand-blue));
  }

  .back-brand {
    position: absolute;
    left: 120px;
    top: 118px;
    display: flex;
    align-items: center;
    gap: 18px;
    color: var(--back-text);
  }
  .back-mark {
    width: 64px;
    height: 64px;
    border-radius: 50%;
    background: var(--deep-blue);
    flex: none;
  }
  .back-name {
    font-family: 'Poppins', sans-serif;
    font-weight: 700;
    font-size: 44px;
    line-height: 1;
  }
  .back-tagline {
    font-family: 'Poppins', sans-serif;
    font-weight: 500;
    font-size: 13px;
    margin-top: 6px;
    letter-spacing: .4px;
  }
</style>
</head>
<body>
  <section class="card card-front">
    <div class="front-info">
      <div class="brand-name">Veltrano.co</div>
      <div class="brand-tagline">Polar Expeditions Specialists</div>
      <div class="person-name">Marcus Hale</div>
      <div class="person-title">President</div>
      <div class="address">4521 Birchwood Road<br>Whitehorse, Canada 28610</div>
      <ul class="contact-list">
        <li>
          <svg class="contact-icon" viewBox="0 0 12 12"><path d="M2.5 1h2l1 3-1.3 1a6 6 0 0 0 2.8 2.8l1-1.3 3 1v2a1 1 0 0 1-1 1A9.5 9.5 0 0 1 1.5 2a1 1 0 0 1 1-1z" fill="#3676b7"/></svg>
          418-592-7063
        </li>
        <li>
          <svg class="contact-icon" viewBox="0 0 12 12"><rect x="2.5" y="1" width="7" height="10" rx="1" fill="none" stroke="#3676b7" stroke-width="1.3"/></svg>
          418-592-7188
        </li>
        <li>
          <svg class="contact-icon" viewBox="0 0 12 12"><rect x="1" y="2.5" width="10" height="7" fill="#3676b7"/><path d="M1 2.5l5 4 5-4" fill="none" stroke="#fff" stroke-width="1"/></svg>
          info@veltrano.com
        </li>
        <li>
          <svg class="contact-icon" viewBox="0 0 12 12"><circle cx="6" cy="6" r="5" fill="#3676b7"/><path d="M1 6h10M6 1c2 2 2 8 0 10M6 1c-2 2-2 8 0 10" fill="none" stroke="#fff" stroke-width=".8"/></svg>
          www.veltrano.com
        </li>
      </ul>
    </div>
    <div class="front-art" role="img" aria-label="Large brand emblem area in icy blue"></div>
  </section>

  <section class="card card-back">
    <div class="back-brand">
      <div class="back-mark"></div>
      <div>
        <div class="back-name">Veltrano.co</div>
        <div class="back-tagline">Polar Expeditions Specialists</div>
      </div>
    </div>
  </section>
</body>
</html>
```